Email Signature Block Design for Law Firm

I would like you to create a similar signature block for my law firm . I saw the email signature block attached as image002.png and wanted a similar design for my law firm. I want to be able to swap the portraits for each of my staff from the final design. Our law firm colors are black, gold, white, red.

Industry/Entity Type

Law

Requirements
Nice to have
• i like the red circle in around the photo in the tall oak group design. The Silver Lark Co desgn is what inspired me to have a signature block design for my firm.

```html
<!DOCTYPE html>
<html lang="en">
<head>
<meta charset="utf-8">
<title>The Harrow Firm – Email Signature</title>
<link rel="stylesheet" href="https://fonts.googleapis.com/css2?family=Cinzel:wght@600;700&family=Poppins:wght@400;500;600;700&display=swap">
<style>
  :root {
    --gold: #d8962a;
    --gold-deep: #c27d18;
    --gold-faint: #f7ead2;
    --ink: #161616;
    --band: #141414;
    --paper: #ffffff;
  }
  * { margin: 0; padding: 0; box-sizing: border-box; }
  html, body { width: 1200px; height: 366px; overflow: hidden; background: var(--paper); }
  .signature { position: relative; width: 1200px; height: 366px; background: var(--paper); color: var(--ink); font-family: "Poppins", sans-serif; }
  .brand { position: absolute; left: 27px; top: 38px; display: flex; align-items: center; gap: 12px; }
  .brand-mark { width: 68px; height: 88px; background: var(--gold); }
  .brand-text { display: flex; flex-direction: column; gap: 6px; }
  .brand-name { font-family: "Cinzel", serif; font-weight: 700; font-size: 22px; color: var(--ink); letter-spacing: 0.5px; white-space: nowrap; }
  .brand-tagline { display: flex; align-items: center; gap: 6px; font-family: "Poppins", sans-serif; font-weight: 600; font-size: 9px; letter-spacing: 5.6px; color: var(--ink); white-space: nowrap; }
  .brand-tagline::before, .brand-tagline::after { content: ""; width: 34px; height: 1px; background: var(--ink); }
  .person-name { position: absolute; left: 25px; top: 166px; font-family: "Cinzel", serif; font-weight: 700; font-size: 41px; line-height: 1; color: var(--ink); white-space: nowrap; letter-spacing: -0.5px; }
  .person-role { position: absolute; left: 26px; top: 214px; font-size: 20px; font-weight: 400; color: var(--ink); }
  .footer-band { position: absolute; left: 0; top: 284px; width: 1200px; height: 82px; background: var(--band); }
  .follow { position: absolute; left: 26px; top: 298px; font-size: 15px; font-weight: 500; letter-spacing: 3.4px; color: var(--paper); line-height: 24px; }
  .social { position: absolute; left: 334px; top: 301px; display: flex; gap: 17px; list-style: none; }
  .social li { width: 18px; height: 18px; border-radius: 50%; background: var(--gold); }
  .website { position: absolute; right: 28px; top: 288px; font-size: 27px; font-weight: 700; letter-spacing: 8.2px; color: var(--paper); line-height: 40px; }
  .portrait-frame { position: absolute; left: 458px; top: 44px; width: 284px; height: 284px; border-radius: 50%; background: var(--paper); padding: 5px; }
  .portrait-ring { width: 100%; height: 100%; border-radius: 50%; background: linear-gradient(135deg, #e9a73a, var(--gold-deep) 60%, #b96f10); padding: 14px; }
  .portrait { width: 100%; height: 100%; border-radius: 50%; background: radial-gradient(circle at 50% 40%, #f1e6d6 0%, #caa983 45%, #2b2b2e 80%); }
  .contact { position: absolute; left: 742px; top: 130px; list-style: none; }
  .contact li { display: flex; align-items: flex-start; gap: 14px; font-size: 19.5px; font-weight: 600; line-height: 22px; color: var(--ink); margin-bottom: 18px; }
  .contact svg { flex: none; width: 22px; height: 22px; margin-top: 0; }
  .watermark-shape { position: absolute; left: 1046px; top: 120px; width: 128px; height: 130px; background: var(--gold-faint); }
</style>
</head>
<body>
<div class="signature">
  <div class="brand">
    <div class="brand-mark"></div>
    <div class="brand-text">
      <span class="brand-name">The Harrow Firm, PLLC</span>
      <span class="brand-tagline">Attorneys At Law</span>
    </div>
  </div>

  <h1 class="person-name">DANIEL R. HARROW</h1>
  <p class="person-role">Personal Injury Lawyer</p>

  <div class="footer-band"></div>
  <p class="follow">FOLLOW US ON</p>
  <ul class="social">
    <li></li><li></li><li></li><li></li><li></li>
  </ul>
  <p class="website">www.harrowfirm.com</p>

  <div class="portrait-frame">
    <div class="portrait-ring">
      <div class="portrait" role="img" aria-label="Staff portrait: attorney in dark suit and blue striped tie, arms crossed"></div>
    </div>
  </div>

  <ul class="contact">
    <li>
      <svg viewBox="0 0 24 24" aria-hidden="true"><circle cx="12" cy="12" r="12" fill="var(--gold)"/><path d="M8.2 6.5l2 2.3-1.2 1.5c.8 1.7 2 2.9 3.7 3.7l1.5-1.2 2.3 2-1 2c-4.4.1-8.5-4-8.4-8.4z" fill="var(--ink)"/></svg>
      555-014-7392
    </li>
    <li>
      <svg viewBox="0 0 24 24" aria-hidden="true"><circle cx="12" cy="12" r="12" fill="var(--gold)"/><path d="M12 5a4.5 4.5 0 0 0-4.5 4.5C7.5 13 12 18.5 12 18.5s4.5-5.5 4.5-9A4.5 4.5 0 0 0 12 5zm0 6.2a1.7 1.7 0 1 1 0-3.4 1.7 1.7 0 0 1 0 3.4z" fill="var(--ink)"/></svg>
      <span>120 Elm Bay St.Suite 300<br>Cedar Point, FL 32000</span>
    </li>
    <li>
      <svg viewBox="0 0 24 24" aria-hidden="true"><circle cx="12" cy="12" r="12" fill="var(--gold)"/><rect x="6" y="8" width="12" height="8.5" fill="var(--ink)"/><path d="M6 8l6 5 6-5" fill="none" stroke="var(--gold)" stroke-width="1"/></svg>
      info@harrowfirm.com
    </li>
  </ul>

  <div class="watermark-shape"></div>
</div>
</body>
</html>
```